Harrowgate Care Assurance Ltd needs a business card and logo

We need a logo for documents, invoices etc and a business card to match. We are a health auditing, training and consulting company based in NZ and working in both Australia and NZ. We ensure health organisations meet all their compliance requirements and develop expertise in the health auditing sector. The design should in some way reflect either symbols for quality management in the health sector.

Target Market(s)

Health providers and those wishing to increase their capability in meeting and understanding compliance requirements

Industry/Entity Type

Business

Contact Information for Business Card

Logo plus contact details

Logo Text

Health auditing, consultancy and training

Requirements
Must have
• Name and contact details director: Marla Fenwick, mfenwick@hca-example.co.nz, PO Box 318, Brackenvale, Northland, cell +6427391652

```html
<!DOCTYPE html>
<html lang="en">
<head>
<meta charset="utf-8">
<title>Harrowgate Care Assurance Ltd – Business Card</title>
<link rel="stylesheet" href="https://fonts.googleapis.com/css2?family=Cinzel:wght@500&family=Montserrat:wght@400;500&display=swap">
<style>
  :root {
    --page-bg: #e6e8eb;
    --card-white: #f7f7f6;
    --brand-blue: #1f86c8;
    --brand-blue-deep: #1a73b8;
    --brand-blue-light: #3d9ad8;
    --brand-green: #5cb85c;
    --ink: #1c1c1c;
    --on-blue: #ffffff;
  }
  html, body {
    margin: 0;
    padding: 0;
    width: 1200px;
    height: 900px;
    overflow: hidden;
    background: var(--page-bg);
  }
  .canvas {
    position: relative;
    width: 1200px;
    height: 900px;
  }
  .card {
    position: absolute;
    left: 250px;
    width: 700px;
    height: 400px;
    box-sizing: border-box;
    box-shadow: 0 6px 18px rgba(0,0,0,0.18);
  }
  .card--back {
    top: 40px;
    background: linear-gradient(135deg, var(--brand-blue-light) 0%, var(--brand-blue) 50%, var(--brand-blue-deep) 100%);
    display: flex;
    align-items: center;
    justify-content: center;
  }
  .card--front {
    top: 460px;
    background: var(--card-white);
    display: flex;
    align-items: center;
    padding: 0 30px 0 36px;
  }
  .brand {
    display: flex;
    flex-direction: column;
    align-items: center;
    gap: 14px;
  }
  .brand__dot {
    width: 58px;
    height: 58px;
    border-radius: 50%;
  }
  .brand__name {
    font-family: 'Cinzel', serif;
    font-weight: 500;
    text-align: center;
    line-height: 1.15;
    letter-spacing: 1px;
    white-space: nowrap;
  }
  .card--back .brand__dot { background: var(--on-blue); }
  .card--back .brand__name { color: var(--on-blue); font-size: 30px; }
  .card--front .brand { width: 290px; flex-shrink: 0; }
  .card--front .brand__dot { background: var(--brand-blue); }
  .card--front .brand__name { color: var(--brand-blue); font-size: 24px; }
  .divider {
    width: 2px;
    height: 150px;
    background: var(--brand-green);
    margin: 0 24px 0 18px;
    flex-shrink: 0;
  }
  .contact {
    font-family: 'Montserrat', sans-serif;
    color: var(--ink);
    font-size: 15px;
    line-height: 1.55;
    white-space: nowrap;
  }
  .contact p { margin: 0; }
  .contact__name {
    color: var(--brand-blue);
    font-weight: 500;
    font-size: 18px;
    letter-spacing: 1px;
    text-transform: uppercase;
    margin-bottom: 4px !important;
  }
  .contact__line { padding-left: 12px; }
  .contact__label { color: var(--brand-blue); display: inline-block; width: 24px; }
  .contact__address { margin-top: 8px !important; }
</style>
</head>
<body>
  <main class="canvas">
    <section class="card card--back" aria-label="Business card back">
      <div class="brand">
        <div class="brand__dot"></div>
        <div class="brand__name">Harrowgate Care<br>Assurance Ltd</div>
      </div>
    </section>

    <section class="card card--front" aria-label="Business card front">
      <div class="brand">
        <div class="brand__dot"></div>
        <div class="brand__name">Harrowgate Care<br>Assurance Ltd</div>
      </div>
      <div class="divider"></div>
      <div class="contact">
        <p class="contact__name">Marla Fenwick</p>
        <p class="contact__line"><span class="contact__label">M:</span>+6427391652</p>
        <p class="contact__line"><span class="contact__label">E:</span>mfenwick@hca-example.co.nz</p>
        <p class="contact__address">PO Box 318, Brackenvale, Northland</p>
      </div>
    </section>
  </main>
</body>
</html>
```